Corporate-Design für Steuerberatungsgesellschaft
Zielgruppe
Wir sind eine Steuerberatungsgesellschaft mit 10 Mitarbeitern im Norden von Deutschland, kurz vor der Ostseeküste. Unser Unternehmen besteht seit 30 Jahren. Wir betreuen vor allem Mandanten in kleinen und mittleren Unternehmen: von der Arztpraxis bis zum Bauunternehmen. Demnächst werden wir neue Räume beziehen. Diese sollen großzügiger und moderner werden, teilweise mit Glaswänden.
Aufgabenstellung
Unser bisheriges Farbkonzept war von bordeaux und creme geprägt (www.kanzlei-mervato.de). Das muss aber nicht weiter bestehen. Das bisherige Logo finden wir inhaltlich recht treffend, aber es sollte moderner gestaltet werden. Der Schriftzug des Kanzleinamens soll an der Fassade in silbernen Buchstaben angebracht werden.

```html
<!DOCTYPE html>
<html lang="de">
<head>
<meta charset="utf-8">
<title>Mervato – Visitenkarten</title>
<link href="https://fonts.googleapis.com/css2?family=Montserrat:wght@400;500;700&display=swap" rel="stylesheet">
<style>
  :root {
    --bordeaux: #5b0f1f;
    --paper: #ffffff;
    --stage: #c9cacc;
    --ink-grey: #6d6d70;
    --ink-dark: #4a4a4d;
  }
  * { margin: 0; padding: 0; box-sizing: border-box; }
  html, body { width: 1200px; height: 852px; overflow: hidden; }
  body {
    background: var(--stage);
    font-family: "Montserrat", Arial, sans-serif;
    position: relative;
  }
  .card {
    position: absolute;
    top: 271px;
    width: 500px;
    height: 310px;
    box-shadow: 0 6px 18px rgba(0,0,0,0.18);
    overflow: hidden;
  }
  .card--front { left: 60px; background: var(--bordeaux); }
  .card--back { left: 640px; background: var(--paper); }

  /* Front */
  .brand {
    position: absolute;
    top: 92px; left: 0; right: 0;
    display: flex; justify-content: center; align-items: center; gap: 14px;
    color: var(--paper);
  }
  .brand__mark {
    width: 34px; height: 34px;
    border: 3px solid var(--paper);
    border-radius: 6px;
  }
  .brand__name {
    font-weight: 700; font-size: 40px; letter-spacing: 1px;
  }
  .services {
    position: absolute;
    top: 214px; left: 0; right: 0; height: 62px;
    background: var(--paper);
    display: flex; flex-direction: column; justify-content: center; align-items: center;
    color: var(--bordeaux); font-size: 13px; line-height: 1.55;
  }
  .front-strip {
    position: absolute; left: 0; right: 0; top: 276px; bottom: 0;
    background: var(--bordeaux);
  }

  /* Back */
  .person { position: absolute; left: 34px; top: 62px; }
  .person__degree { font-size: 13px; color: var(--ink-grey); margin-left: 22px; }
  .person__name {
    display: flex; align-items: center; gap: 10px;
    font-weight: 700; font-size: 22px; color: var(--bordeaux); margin: 2px 0;
  }
  .person__name::before {
    content: ""; width: 12px; height: 14px; background: var(--bordeaux);
  }
  .person__role { font-size: 13px; color: var(--ink-grey); margin-left: 22px; }

  .address {
    position: absolute; left: 56px; top: 186px;
    font-size: 12px; line-height: 1.55; color: var(--ink-grey);
  }
  .address strong { color: var(--ink-dark); font-weight: 700; }

  .contact {
    position: absolute; left: 286px; top: 190px;
    list-style: none; font-size: 11.5px; line-height: 1.65; color: var(--ink-grey);
  }
  .contact li { display: flex; align-items: center; gap: 8px; }
  .contact svg { width: 12px; height: 12px; flex: none; }

  .back-strip {
    position: absolute; left: 0; right: 0; bottom: 0; height: 14px;
    background: var(--bordeaux);
  }
</style>
</head>
<body>

<section class="card card--front" aria-label="Visitenkarte Vorderseite">
  <div class="brand">
    <span class="brand__mark"></span>
    <span class="brand__name">MERVATO</span>
  </div>
  <div class="services">
    <span>Steuerberatung / Finanz- und Lohnbuchhaltung</span>
    <span>Betriebswirtschaftliche Beratung</span>
  </div>
  <div class="front-strip"></div>
</section>

<section class="card card--back" aria-label="Visitenkarte Rückseite">
  <div class="person">
    <p class="person__degree">Diplom-Kaufmann</p>
    <p class="person__name">Jonas Lindqvist - Brandt</p>
    <p class="person__role">Geschäftsführer / Steuerberater</p>
  </div>

  <address class="address" style="font-style:normal">
    Mervato<br>
    <strong>Steuerberatungsgesellschaft mbH</strong><br>
    Lindenweg 12<br>
    18000 Musterhafen
  </address>

  <ul class="contact">
    <li><svg viewBox="0 0 12 12"><circle cx="6" cy="6" r="6" fill="#5b0f1f"/><path d="M4 3.5l1 1.5-.6.7a4 4 0 0 0 1.9 1.9l.7-.6 1.5 1-.6.9C5.6 8.9 3.1 6.4 3.1 4.1z" fill="#fff"/></svg>+49 (0) 3000 / 55 21 - 0</li>
    <li><svg viewBox="0 0 12 12"><circle cx="6" cy="6" r="6" fill="#5b0f1f"/><rect x="3.5" y="4.5" width="5" height="4" fill="#fff"/><rect x="4.3" y="3" width="3.4" height="1.5" fill="#fff"/></svg>+49 (0) 3000 / 55 21 - 14</li>
    <li><svg viewBox="0 0 12 12"><circle cx="6" cy="6" r="6" fill="#5b0f1f"/><rect x="3" y="4" width="6" height="4.2" fill="#fff"/><path d="M3 4l3 2.3L9 4" stroke="#5b0f1f" stroke-width=".7" fill="none"/></svg>musterhafen@kanzlei-mervato.de</li>
    <li><svg viewBox="0 0 12 12"><circle cx="6" cy="6" r="6" fill="#5b0f1f"/><circle cx="6" cy="6" r="3" fill="none" stroke="#fff" stroke-width=".8"/><path d="M3 6h6M6 3v6" stroke="#fff" stroke-width=".7"/></svg>www.kanzlei-mervato.de</li>
  </ul>

  <div class="back-strip"></div>
</section>

</body>
</html>
```